KBT Business Cards

We require business cards for our business. We would like a matte black back to the card, with our logo centred in the middle. The front side of the card is open to design.

Target Market(s)

Clients looking for legal services (professional)

Industry/Entity Type

Legal

Contact Information for Business Card

Doran Kelbrath
Partner
Mobile: 0461 738 524
Email: doran@kbtlaw.co
Website: www.kbtlaw.co
Level 3, 118 Wendmore Street
Sydney NSW 2000

Font styles to use
Other font styles liked:
• Avenir

Colors
f04a50
ffffff
1b1b1b

Requirements
Must have
• Black back with logo included in the centre of the card.
• Our font is Avenir.

```html
<!DOCTYPE html>
<html lang="en">
<head>
<meta charset="utf-8">
<title>KBT Business Cards</title>
<link rel="stylesheet" href="https://fonts.googleapis.com/css2?family=Nunito+Sans:wght@400;600;800&display=swap">
<style>
  :root {
    --stage: #d8d3cb;
    --card-black: #141414;
    --card-black-soft: #1f1f1f;
    --accent: #d92d63;
    --white: #ffffff;
    --muted: #e6e6e6;
  }
  * { margin: 0; padding: 0; box-sizing: border-box; }
  html, body { width: 1200px; height: 780px; overflow: hidden; }
  body {
    background: var(--stage);
    font-family: "Nunito Sans", "Avenir", sans-serif;
    position: relative;
  }
  .card {
    position: absolute;
    top: 235px;
    width: 540px;
    height: 309px;
    border-radius: 4px;
    background: radial-gradient(ellipse at 60% 40%, var(--card-black-soft), var(--card-black) 75%);
    box-shadow: 0 10px 30px rgba(0,0,0,0.25);
    overflow: hidden;
  }
  .card--front { left: 40px; }
  .card--back { left: 620px; }
  .accent-rule {
    position: absolute;
    left: 0; right: 0;
    height: 3px;
    background: var(--accent);
  }
  .accent-rule--top { top: 16px; }
  .accent-rule--bottom { bottom: 16px; }

  .front-mark {
    position: absolute;
    top: 52px;
    right: 56px;
    display: flex;
    align-items: center;
    gap: 12px;
  }
  .front-mark .mark-square {
    width: 22px; height: 22px;
    background: var(--accent);
  }
  .front-mark .mark-name {
    font-weight: 800;
    font-size: 54px;
    letter-spacing: 4px;
    color: var(--white);
    line-height: 1;
  }

  .holder {
    position: absolute;
    left: 38px;
    top: 150px;
  }
  .holder-name {
    color: var(--accent);
    font-weight: 800;
    font-size: 17px;
    letter-spacing: 0.5px;
    text-transform: uppercase;
  }
  .holder-title {
    color: var(--white);
    font-size: 14px;
    margin-top: 2px;
  }

  .contact {
    position: absolute;
    left: 210px;
    top: 176px;
    color: var(--muted);
    font-size: 13px;
    line-height: 18px;
  }
  .contact-address { margin-bottom: 8px; }
  .contact-list { list-style: none; }
  .contact-list li {
    display: flex;
    align-items: center;
    gap: 8px;
  }
  .contact-list svg { width: 11px; height: 11px; flex: none; }

  .back-mark {
    position: absolute;
    inset: 0;
    display: flex;
    flex-direction: column;
    align-items: center;
    justify-content: center;
    gap: 12px;
  }
  .back-mark .mark-row {
    display: flex;
    align-items: center;
    gap: 12px;
  }
  .back-mark .mark-square {
    width: 18px; height: 18px;
    background: var(--accent);
  }
  .back-mark .mark-name {
    font-weight: 800;
    font-size: 46px;
    letter-spacing: 4px;
    color: var(--white);
    line-height: 1;
  }
  .back-mark .firm-name {
    font-weight: 800;
    font-size: 17px;
    letter-spacing: 2px;
    color: var(--white);
    text-transform: uppercase;
  }
</style>
</head>
<body>
  <section class="card card--front" aria-label="Card front">
    <div class="accent-rule accent-rule--top"></div>
    <div class="accent-rule accent-rule--bottom"></div>

    <div class="front-mark">
      <span class="mark-square"></span>
      <span class="mark-name">KBT</span>
    </div>

    <div class="holder">
      <p class="holder-name">Doran Kelbrath</p>
      <p class="holder-title">Partner</p>
    </div>

    <div class="contact">
      <p class="contact-address">Level 3, 118 Wendmore Street<br>Sydney NSW 2000</p>
      <ul class="contact-list">
        <li>
          <svg viewBox="0 0 11 11" aria-hidden="true"><rect x="1.5" y="0.5" width="8" height="10" rx="1" fill="none" stroke="#ffffff" stroke-width="1"/></svg>
          0461 738 524
        </li>
        <li>
          <svg viewBox="0 0 11 11" aria-hidden="true"><rect x="0.5" y="2" width="10" height="7" fill="#d92d63"/><path d="M0.5 2 L5.5 6 L10.5 2" fill="none" stroke="#ffffff" stroke-width="0.9"/></svg>
          doran@kbtlaw.co
        </li>
        <li>
          <svg viewBox="0 0 11 11" aria-hidden="true"><circle cx="5.5" cy="5.5" r="5" fill="#d92d63"/></svg>
          www.kbtlaw.co
        </li>
      </ul>
    </div>
  </section>

  <section class="card card--back" aria-label="Card back">
    <div class="accent-rule accent-rule--top"></div>
    <div class="accent-rule accent-rule--bottom"></div>
    <div class="back-mark">
      <div class="mark-row">
        <span class="mark-square"></span>
        <span class="mark-name">KBT</span>
      </div>
      <p class="firm-name">Kelbrath Brant Legal</p>
    </div>
  </section>
</body>
</html>
```